Brenlow Estates Website and Logo Design

We need a new logo and website designed for 'Brenlow Estates Ltd', which is a well established Guernsey property holding company founded in 1934.

The company does not currently have a website. The new website should be similar in style and layout to https://www.quorvanhall.example/.

Target Market(s)

Industry, Media, Tenants

Industry/Entity Type

Property Management

Logo Text

BEL OR Brenlow Estates Ltd OR BE

Coding

Coded - Design and coding required

Number of Pages Required

4 page

Font styles to use
Other font styles liked:
• Helvetica

Requirements
Must have
• The logo laying over the picture (like https://www.quorvanhall.example/).
• Big pictures on homepage (like https://www.quorvanhall.example/)

```html
<!DOCTYPE html>
<html lang="en">
<head>
<meta charset="utf-8">
<title>Brenlow Estates Ltd</title>
<link rel="stylesheet" href="https://fonts.googleapis.com/css2?family=Open+Sans:wght@400;600;700&family=Roboto+Slab:wght@400;700&display=swap">
<style>
:root{
  --blue:#0a9be6;
  --blue-dark:#0784c7;
  --ink:#1b1b1b;
  --text:#555;
  --white:#fff;
  --light:#efefef;
  --footer:#222;
  --slab:"Roboto Slab", Georgia, serif;
  --sans:"Open Sans", Arial, sans-serif;
}
*{box-sizing:border-box;margin:0;padding:0}
html,body{width:1200px;height:2830px;overflow:hidden}
body{position:relative;font-family:var(--sans);color:var(--text);background:var(--white)}
.abs{position:absolute}

/* header */
.site-header{position:absolute;left:0;top:0;width:1200px;height:125px;background:var(--white)}
.top-bar{position:absolute;left:620px;top:0;width:580px;height:42px;background:var(--blue);color:var(--white);font-size:15px}
.top-bar .item{position:absolute;top:11px;display:flex;align-items:center;gap:10px}
.brand{position:absolute;left:75px;top:14px;display:flex;align-items:center;gap:14px}
.brand-mark{width:84px;height:84px;border-radius:50%;border:4px solid var(--blue)}
.brand-name{font-family:var(--slab);font-weight:700;color:var(--blue);font-size:36px;line-height:38px}
.brand-name small{display:block;font-size:22px;line-height:26px;font-weight:700}
.main-nav{position:absolute;top:62px;left:513px;display:flex;font-family:var(--slab);font-size:18px;color:#777}
.main-nav a{color:inherit;text-decoration:none;height:44px;line-height:44px;margin-right:48px}
.main-nav a.active{background:var(--blue);color:var(--white);padding:0 22px;border-radius:2px;margin-right:50px}

/* hero */
.hero{position:absolute;left:0;top:125px;width:1200px;height:573px;
  background:linear-gradient(180deg,#6d7378 0%,#4b5257 45%,#3a4146 75%,#5d6367 100%);text-align:center;color:var(--white)}
.hero h1{position:absolute;top:205px;width:100%;font-family:var(--slab);font-weight:700;font-size:52px;letter-spacing:1px}
.hero p{position:absolute;top:285px;width:100%;font-size:24px}
.btn-hero{position:absolute;left:500px;top:345px;width:200px;height:49px;line-height:49px;border-radius:25px;background:var(--white);color:var(--blue);font-weight:700;font-size:18px}

/* welcome */
.welcome{position:absolute;left:0;top:698px;width:1200px;height:623px;background:var(--blue);color:var(--white);text-align:center}
.section-title{font-family:var(--slab);font-weight:400;font-size:40px}
.welcome .section-title{position:absolute;top:48px;width:100%}
.welcome .lead{position:absolute;left:155px;top:115px;width:890px;font-size:15px;line-height:25px}
.timeline-item{position:absolute;top:236px;width:340px;text-align:center}
.timeline-photo{width:216px;height:216px;margin:0 auto;border-radius:50%;border:5px solid var(--white)}
.timeline-item h3{font-family:var(--slab);font-weight:400;font-size:26px;margin-top:16px}
.timeline-item p{font-size:15px;line-height:25px;margin-top:4px}

/* about */
.about{position:absolute;left:0;top:1321px;width:1200px;height:368px;background:var(--white)}
.about .section-title{position:absolute;left:81px;top:50px;color:var(--ink);font-size:42px}
.about .section-title span,.contact .section-title span{color:var(--blue)}
.about p{position:absolute;left:81px;top:117px;width:624px;font-size:16px;line-height:24.5px;letter-spacing:.2px}
.btn-more{position:absolute;left:77px;top:268px;width:170px;height:49px;line-height:49px;border-radius:25px;background:var(--blue);color:var(--white);font-size:18px;text-align:center}
.video{position:absolute;left:749px;top:62px;width:374px;height:255px;border:5px solid #ccc;
  background:linear-gradient(180deg,#5a7688 0%,#34505f 55%,#213540 100%)}

/* projects */
.projects{position:absolute;left:0;top:1689px;width:1200px;height:500px;
  background:linear-gradient(180deg,#4fb3ee 0%,#2f9ee0 50%,#1e90d6 100%);color:var(--white);text-align:center}
.projects .section-title{position:absolute;top:50px;width:100%}
.projects .lead{position:absolute;top:119px;width:100%;font-size:15px;line-height:25px}
.project{position:absolute;top:213px;width:236px;text-align:center}
.project-photo{width:236px;height:142px}
.project h3{font-family:var(--slab);font-weight:400;font-size:24px;margin-top:12px}
.project p{font-size:15px;line-height:25px;margin-top:4px}

/* contact */
.contact{position:absolute;left:0;top:2189px;width:1200px;height:339px;background:var(--light)}
.contact .section-title{position:absolute;top:40px;width:100%;text-align:center;color:var(--ink)}
.field{position:absolute;background:var(--white);border:1px solid #ddd;border-radius:3px;font-size:14px;color:#999;padding:10px 22px}
.btn-submit{position:absolute;left:460px;top:2434px;width:625px;height:42px;line-height:42px;background:var(--blue);color:var(--white);text-align:center;font-size:22px;border-radius:2px}

/* footer */
.site-footer{position:absolute;left:0;top:2528px;width:1200px;height:255px;background:var(--footer);color:var(--white)}
.footer-mark{position:absolute;left:151px;top:28px;width:56px;height:56px;border-radius:50%;border:3px solid var(--blue)}
.footer-name{position:absolute;left:80px;top:98px;width:200px;text-align:center;font-family:var(--slab);font-weight:700;color:var(--blue);font-size:24px;line-height:26px}
.footer-name small{display:block;font-size:15px;line-height:18px}
.social{position:absolute;top:160px;width:52px;height:52px;border-radius:50%}
.social.blue{background:var(--blue)}
.social.white{background:var(--white)}
.footer-col{position:absolute;top:30px;font-size:15px}
.footer-col h4{font-family:var(--slab);font-weight:400;font-size:21px;margin-bottom:18px}
.footer-col li{list-style:none;line-height:31px}
.footer-col p{line-height:24px}
.client{color:var(--blue);font-weight:700;font-size:14px;margin-top:2px}
.arrows{display:flex;gap:11px;margin-top:16px}
.arrows span{width:30px;height:30px;background:#444;display:flex;align-items:center;justify-content:center}
.contact-line{display:flex;align-items:flex-start;gap:12px;line-height:28px;margin-bottom:12px}
.contact-line svg{flex:none;margin-top:6px}
.copyright{position:absolute;left:0;top:2783px;width:1200px;height:47px;line-height:47px;background:var(--blue);color:var(--white);text-align:center;font-size:15px}
</style>
</head>
<body>

<header class="site-header">
  <div class="top-bar">
    <div class="item" style="left:35px">
      <svg width="18" height="13" viewBox="0 0 18 13"><rect x="0" y="0" width="18" height="13" fill="#fff"/><path d="M0 0 L9 7 L18 0" fill="none" stroke="#0a9be6" stroke-width="1.6"/></svg>
      Lorem Ipsum is simply dummy
    </div>
    <div class="item" style="left:365px;font-weight:700">
      <svg width="16" height="16" viewBox="0 0 16 16"><path d="M3 1 L6 1 L7 5 L5 6.5 C6 9 7 10 9.5 11 L11 9 L15 10 L15 13 C15 14 14 15 13 15 C6 15 1 10 1 3 C1 2 2 1 3 1Z" fill="#fff"/></svg>
      123 456 7890
    </div>
  </div>
  <div class="brand">
    <div class="brand-mark"></div>
    <div class="brand-name">Brenlow<small>Estates Ltd</small></div>
  </div>
  <nav class="main-nav">
    <a class="active">HOME</a><a>ABOUT</a><a>PROJECTS</a><a>NEWS</a><a>CONTACT</a>
  </nav>
</header>

<section class="hero" role="img" aria-label="City skyline with high-rise towers beside the waterfront">
  <h1>BRENLOW ESTATES LTD</h1>
  <p>Lorem Ipsum is simply dummy text of the printing and typesetting industry.</p>
  <div class="btn-hero">CONTACT US NOW</div>
</section>

<section class="welcome">
  <h2 class="section-title">WELCOME TO BRENLOW ESTATES LTD</h2>
  <p class="lead">Brenlow Estates Limited (BEL) is a family-owned Guernsey property holding company. It purchases properties that are considered to have potential for development either through refurbishment or by obtaining planning permission to change its classification from, for example, industrial premises to offices or retail outlets.</p>

  <div class="timeline-item" style="left:73px">
    <div class="timeline-photo" role="img" aria-label="Harbour with white buildings and moored boats" style="background:linear-gradient(180deg,#8fc3ea 0%,#d9d6cc 55%,#3d7fa6 100%)"></div>
    <h3>YESTERDAY</h3>
    <p>BEL was founded in 1934 by Arthur Brenlow to manage both his own extensive investments and his property...</p>
  </div>
  <div class="timeline-item" style="left:434px">
    <div class="timeline-photo" role="img" aria-label="Aerial view of a marina and waterfront development" style="background:linear-gradient(180deg,#6f8e9e 0%,#8ba2a7 45%,#3f7796 100%)"></div>
    <h3>TODAY</h3>
    <p>The Brenlow family has steadily built on the foundations set out by the founder and each generation develops and...</p>
  </div>
  <div class="timeline-item" style="left:790px">
    <div class="timeline-photo" role="img" aria-label="Modern city towers under a cloudy sky" style="background:linear-gradient(180deg,#c9d6e0 0%,#8e9ba4 55%,#4f6c5a 100%)"></div>
    <h3>TOMORROW</h3>
    <p>In keeping with its past project development philosophy, its intrinsic understanding of the local property mark...</p>
  </div>
</section>

<section class="about">
  <h2 class="section-title">ABOUT <span>BRENLOW ESTATES LTD</span></h2>
  <p>Lorem Ipsum is simply dummy text of the printing and typesetting industry. Lorem Ipsum has been the industry's standard dummy text ever since the 1500s, when an unknown printer took a galley of type and scrambled it to make a type specimen book. It has survived not only five centuries, but also the leap into electronic typesetting, remaining essentially unchanged. It was popularised in the 1960.</p>
  <div class="btn-more">READ MORE &#187;</div>
  <div class="video" role="img" aria-label="Video still of boats in a bay below limestone cliffs">
    <svg class="abs" style="left:150px;top:90px" width="64" height="64" viewBox="0 0 64 64"><circle cx="32" cy="32" r="30" fill="rgba(0,0,0,.55)"/><path d="M25 19 L46 32 L25 45Z" fill="#fff"/></svg>
  </div>
</section>

<section class="projects" aria-label="Our projects" >
  <h2 class="section-title">OUR PROJECTS</h2>
  <p class="lead">Lorem Ipsum is simply dummy text of the printing and typesetting industry.<br>Lorem Ipsum has a been the industry's standard.</p>

  <div class="project" style="left:77px">
    <div class="project-photo" role="img" aria-label="Harbour with yachts and white apartments" style="background:linear-gradient(180deg,#8ec4ec 0%,#e1ddd2 55%,#3b7ea7 100%)"></div>
    <h3>Lorem Ipsum Is</h3>
    <p>Lorem Ipsum is simply dummy text of... READ MORE &#187;</p>
  </div>
  <div class="project" style="left:349px">
    <div class="project-photo" role="img" aria-label="Downtown skyscrapers by the water" style="background:linear-gradient(180deg,#c7d4de 0%,#8c99a2 55%,#4f6b5b 100%)"></div>
    <h3>Lorem Ipsum Is</h3>
    <p>Lorem Ipsum is simply dummy text of... READ MORE &#187;</p>
  </div>
  <div class="project" style="left:619px">
    <div class="project-photo" role="img" aria-label="Marina with boats and hillside town" style="background:linear-gradient(180deg,#8fb6d6 0%,#cfcabd 55%,#4a7f9d 100%)"></div>
    <h3>Lorem Ipsum Is</h3>
    <p>Lorem Ipsum is simply dummy text of... READ MORE &#187;</p>
  </div>
  <div class="project" style="left:891px">
    <div class="project-photo" role="img" aria-label="Aerial view of a waterfront resort and harbour" style="background:linear-gradient(180deg,#6e8d9d 0%,#8ea3a6 45%,#3c7594 100%)"></div>
    <h3>Lorem Ipsum Is</h3>
    <p>Lorem Ipsum is simply dummy text of... READ MORE &#187;</p>
  </div>
</section>

<section class="contact">
  <h2 class="section-title">CONTACT <span>US</span></h2>
</section>
<div class="field" style="left:115px;top:2332px;width:332px;height:40px">Name</div>
<div class="field" style="left:115px;top:2383px;width:332px;height:42px">E - Mail</div>
<div class="field" style="left:115px;top:2434px;width:332px;height:42px">Phone</div>
<div class="field" style="left:460px;top:2332px;width:625px;height:91px">Message</div>
<div class="btn-submit">SUBMIT</div>

<footer class="site-footer">
  <div class="footer-mark"></div>
  <div class="footer-name">Brenlow<small>Estates Ltd</small></div>
  <div class="social blue" style="left:76px" aria-label="Social link"></div>
  <div class="social white" style="left:151px" aria-label="Social link"></div>
  <div class="social white" style="left:223px" aria-label="Social link"></div>

  <div class="footer-col" style="left:351px">
    <h4>Useful Links</h4>
    <ul><li>Home</li><li>About</li><li>Projects</li><li>News</li><li>Contact</li></ul>
  </div>
  <div class="footer-col" style="left:621px;width:210px">
    <h4>Client Testimonial</h4>
    <p>Lorem Ipsum is simply dummy text of the printing and typesetting industry...</p>
    <div class="client">- CLIENT NAME</div>
    <div class="arrows">
      <span><svg width="10" height="14" viewBox="0 0 10 14"><path d="M8 1 L2 7 L8 13" fill="none" stroke="#fff" stroke-width="2"/></svg></span>
      <span><svg width="10" height="14" viewBox="0 0 10 14"><path d="M2 1 L8 7 L2 13" fill="none" stroke="#fff" stroke-width="2"/></svg></span>
    </div>
  </div>
  <div class="footer-col" style="left:891px;width:240px">
    <h4>Contact Us</h4>
    <div class="contact-line"><svg width="14" height="18" viewBox="0 0 14 18"><path d="M7 0 C3 0 0 3 0 7 C0 12 7 18 7 18 C7 18 14 12 14 7 C14 3 11 0 7 0Z" fill="#0a9be6"/><circle cx="7" cy="7" r="2.5" fill="#222"/></svg><span>Lorem Ipsum is simply dummy text of the printing.</span></div>
    <div class="contact-line" style="font-weight:700"><svg width="16" height="16" viewBox="0 0 16 16"><path d="M3 1 L6 1 L7 5 L5 6.5 C6 9 7 10 9.5 11 L11 9 L15 10 L15 13 C15 14 14 15 13 15 C6 15 1 10 1 3 C1 2 2 1 3 1Z" fill="#0a9be6"/></svg><span>123 456 7890</span></div>
    <div class="contact-line"><svg width="18" height="13" viewBox="0 0 18 13"><rect x="1" y="1" width="16" height="11" fill="none" stroke="#0a9be6" stroke-width="1.6"/><path d="M1 1 L9 7 L17 1" fill="none" stroke="#0a9be6" stroke-width="1.6"/></svg><span>Lorem Ipsum is simply</span></div>
  </div>
</footer>
<div class="copyright">&#169; <strong>BRENLOW ESTATES LTD</strong> - 2016. All Rights Reserved.</div>

</body>
</html>
```